Consulting firm need a professional powerpoint design

A startup Climate change firm needs a powerpoint template design. The design should reflect aspects of climate change adaptation, resilience and environmental sustainability.

The powerpoint design must convey aspects of nature and climate action for a resilient society.

The last slide of the powerpoint must have a allocation for a slogan such as 'Connecting evidence and action'.

Use the colors in the logo and business card for the powerpoint design.

Target Market(s)

Government and industry

Font styles to use
Sans Serif
Other font styles liked:
• nexa font family

Colors
85cae6
abd037
fece3e

Requirements
Must have
• - Colors used in logo and business card
- Convey science and nature
- Professional
Nice to have
• Many pages
Should not have
• Not complicated

```html
<!DOCTYPE html>
<html lang="en">
<head>
<meta charset="utf-8">
<title>Terravanta Presentation Deck</title>
<link href="https://fonts.googleapis.com/css2?family=Montserrat:wght@300;400;500;600;700;800&display=swap" rel="stylesheet">
<style>
:root{
  --navy:#1d3257;--navy-soft:#2c4570;--green:#3fa535;--lime:#abd037;--sky:#85cae6;--blue:#1f8fc7;
  --sun:#fece3e;--amber:#f6a318;--ink:#1f2a3c;--grey:#6b7280;--mist:#f1f2f4;--paper:#ffffff;--canvas:#e9e9ea;
}
*{box-sizing:border-box;margin:0;padding:0}
html,body{width:1200px;height:2338px;overflow:hidden;background:var(--canvas)}
body{font-family:"Montserrat",sans-serif;color:var(--ink)}
.sheet{position:relative;width:1200px;height:2338px}
.hero{position:absolute;left:0;top:0;width:1200px;height:495px;background:linear-gradient(100deg,#7d7c78 0%,#a9a7a1 30%,#d6d5d2 55%,var(--canvas) 75%)}
.hero-title{position:absolute;left:71px;top:180px;font-size:60px;font-weight:800;color:var(--green);letter-spacing:-.5px;line-height:1}
.hero-sub{position:absolute;left:197px;top:244px;font-size:60px;font-weight:500;color:#222;line-height:1}
.showcase{position:absolute;left:561px;top:86px;width:470px;height:263px;overflow:hidden;box-shadow:0 4px 18px rgba(0,0,0,.18)}
.showcase .slide{left:0;top:0;transform:scale(1.224);transform-origin:0 0}
.slide{position:absolute;width:384px;height:215px;background:var(--paper);overflow:hidden;font-size:4px;line-height:1.5}
.abs{position:absolute}
.brand{position:absolute;display:flex;align-items:center;gap:3px;font-weight:700;font-size:6.5px;letter-spacing:.6px;color:var(--navy)}
.brand i{display:block;width:8px;height:8px;border-radius:50%;background:var(--green)}
.brand.light{color:var(--paper)}
.head{position:absolute;left:0;top:0;width:384px;height:27px;background:var(--navy)}
.head h3{position:absolute;left:8px;top:6px;font-size:8.5px;font-weight:700;color:var(--paper);letter-spacing:-.1px}
.head .tag{position:absolute;left:8px;top:16px;font-size:4.2px;font-weight:700;color:var(--sun);letter-spacing:1.2px}
.head .brand{right:9px;top:9px;color:var(--paper)}
.stripe{position:absolute;left:0;top:27px;width:384px;height:2px;background:linear-gradient(90deg,var(--paper) 0 40%,var(--lime) 40% 62%,var(--sky) 62% 82%,var(--sun) 82%)}
.foot{position:absolute;left:0;bottom:0;width:384px;height:5px;background:var(--navy)}
.foot-stripe{position:absolute;right:0;bottom:5px;width:200px;height:2px;background:linear-gradient(90deg,var(--lime) 0 35%,var(--sky) 35% 68%,var(--sun) 68%)}
.copy{position:absolute;left:12px;bottom:7px;font-size:3.6px;color:var(--ink)}
.photo{position:absolute}
.dot{position:absolute;border-radius:50%;display:flex;align-items:center;justify-content:center;color:var(--paper);font-weight:700}
.lbl{font-weight:700;font-size:5px;color:var(--ink)}
.txt{font-size:3.7px;color:var(--grey);line-height:1.5}
.navy-box{position:absolute;background:var(--navy);color:var(--paper)}
.card{position:absolute;top:57px;width:88px;height:133px;border-radius:7px;text-align:center;color:var(--paper)}
.card .disc{width:50px;height:50px;border-radius:50%;background:var(--paper);margin:8px auto 0}
.card b{display:block;margin-top:20px;font-size:5px}
.card p{font-size:3.8px;margin:3px 8px 0}
.tile{position:absolute;width:62px;height:20px;border-radius:2px;display:flex;align-items:center;justify-content:center;text-align:center;color:var(--paper);font-size:3.5px;padding:0 4px}
.team{position:absolute;top:40px;width:86px;height:150px;padding:30px 8px 0}
.team .face{width:26px;height:26px;border-radius:50%;background:linear-gradient(#6f7a85,#2f3a46)}
.team b{display:block;margin-top:5px;font-size:6px;font-weight:500;color:var(--navy)}
.team em{display:block;font-style:normal;font-size:5.5px;color:var(--grey);line-height:1.2}
.team p{margin-top:5px}
.team .line{position:absolute;left:0;bottom:0;width:100%;height:2px}
.grid{position:absolute;border-collapse:collapse;font-size:3.8px;text-align:center}
.grid th{color:var(--blue);font-weight:600;border-top:1px solid var(--blue);border-bottom:1px solid var(--blue);height:10px}
.grid td{height:10px;color:var(--ink)}
.grid tr:nth-child(even) td{background:var(--mist)}
.step{position:absolute;height:9px;background:var(--navy);color:var(--paper);font-size:4.5px;font-weight:700;text-align:right;padding-right:4px;line-height:9px}
.toc li{list-style:none;display:flex;gap:18px;height:15.5px;font-size:5px;color:var(--grey)}
.toc li span{width:8px}
.plan th{height:15px;background:var(--navy);color:var(--paper);font-size:4.6px;font-weight:700;text-align:left;padding-left:5px}
.plan td{vertical-align:top;padding:6px 5px 0;height:40px;width:79px}
.plan td b{font-size:4.3px;color:var(--ink)}
.plan .hl{background:var(--navy)}
.plan .hl b,.plan .hl .txt{color:var(--paper)}
</style>
</head>
<body>
<main class="sheet">

  <section class="hero" role="img" aria-label="Crowd of young climate activists raising their hands at sunset"></section>
  <h1 class="hero-title">Presentation</h1>
  <p class="hero-sub">Deck</p>

  <div class="showcase">
    <article class="slide">
      <div class="photo" style="left:0;top:0;width:200px;height:215px;background:linear-gradient(90deg,#7c6f60,#c9c2b6 60%,#ffffff)" role="img" aria-label="Protester holding a hand-painted sign about protecting the planet"></div>
      <svg class="abs" style="left:0;top:20px" width="80" height="150" viewBox="0 0 80 150"><path d="M0 0 Q80 40 60 130 L0 150Z" fill="var(--green)"/><path d="M0 100 Q40 120 55 150 L0 150Z" fill="var(--blue)"/></svg>
      <div class="brand" style="left:194px;top:56px"><i></i>TERRAVANTA</div>
      <p class="abs" style="left:194px;top:98px;font-size:13px;font-weight:500;color:var(--navy)">ADD YOUR AWESOME</p>
      <p class="abs" style="left:193px;top:112px;font-size:25px;font-weight:300;color:var(--navy);letter-spacing:1.5px">TITLE HERE</p>
      <p class="abs" style="left:195px;top:146px;font-size:5.5px;letter-spacing:3px;color:var(--navy)">HERE ADD YOUR SUBTITLE</p>
      <p class="abs" style="left:196px;top:192px;font-size:6.5px;letter-spacing:3px;color:var(--navy)">2020</p>
    </article>
  </div>

  <!-- Row 1 -->
  <article class="slide" style="left:13px;top:498px">
    <div class="photo" style="left:0;top:0;width:200px;height:215px;background:linear-gradient(90deg,#7c6f60,#c9c2b6 60%,#ffffff)" role="img" aria-label="Protester holding a hand-painted sign about protecting the planet"></div>
    <svg class="abs" style="left:0;top:20px" width="80" height="150" viewBox="0 0 80 150"><path d="M0 0 Q80 40 60 130 L0 150Z" fill="var(--green)"/><path d="M0 100 Q40 120 55 150 L0 150Z" fill="var(--blue)"/></svg>
    <div class="brand" style="left:194px;top:56px"><i></i>TERRAVANTA</div>
    <p class="abs" style="left:194px;top:98px;font-size:13px;font-weight:500;color:var(--navy)">ADD YOUR AWESOME</p>
    <p class="abs" style="left:193px;top:112px;font-size:25px;font-weight:300;color:var(--navy);letter-spacing:1.5px">TITLE HERE</p>
    <p class="abs" style="left:195px;top:146px;font-size:5.5px;letter-spacing:3px;color:var(--navy)">HERE ADD YOUR SUBTITLE</p>
    <p class="abs" style="left:196px;top:192px;font-size:6.5px;letter-spacing:3px;color:var(--navy)">2020</p>
  </article>

  <article class="slide" style="left:408px;top:498px;background:linear-gradient(180deg,#2f4a72,#1f3559 55%,#35496a)" role="img" aria-label="Wind turbine standing over misty mountains at dusk">
    <div class="brand light" style="left:136px;top:60px"><i></i>TERRAVANTA</div>
    <p class="abs" style="left:0;width:384px;top:96px;text-align:center;font-size:13px;font-weight:500;color:var(--paper)">ADD YOUR AWESOME</p>
    <p class="abs" style="left:0;width:384px;top:109px;text-align:center;font-size:23px;font-weight:300;color:var(--paper);letter-spacing:1.5px">TITLE HERE</p>
    <p class="abs" style="left:0;width:384px;top:138px;text-align:center;font-size:5.5px;letter-spacing:3px;color:var(--paper)">HERE ADD YOUR SUBTITLE</p>
    <p class="abs" style="left:0;width:384px;top:200px;text-align:center;font-size:5.5px;letter-spacing:3px;color:var(--paper)">2020</p>
  </article>

  <article class="slide" style="left:804px;top:498px">
    <div class="photo" style="left:0;top:0;width:118px;height:215px;background:radial-gradient(circle at 55% 55%,#c9762b,#3a1f0e 60%,#120a05)" role="img" aria-label="Hands cupping a glowing globe"></div>
    <div class="brand light" style="left:22px;top:110px"><i></i>TERRAVANTA</div>
    <div class="navy-box" style="left:118px;top:0;width:26px;height:215px"></div>
    <p class="abs" style="left:131px;top:108px;transform:translate(-50%,-50%) rotate(-90deg);white-space:nowrap;font-size:10px;font-weight:700;color:var(--paper)">TABLE OF CONTENTS</p>
    <ol class="toc abs" style="left:228px;top:37px">
      <li><span>i.</span>Introduction</li><li><span>ii.</span>About Us</li><li><span>iii.</span>Welcome Message</li>
      <li><span>iv.</span>Company Profile</li><li><span>v.</span>Team</li><li><span>vi.</span>Team Group</li>
      <li><span>vii.</span>Portfolio</li><li><span>viii.</span>Info graphic</li><li><span>ix.</span>Contact Us</li><li><span>x.</span>Data Chart</li>
    </ol>
  </article>

  <!-- Row 2 -->
  <article class="slide" style="left:13px;top:727px">
    <div class="head"><div class="brand light" style="right:9px;top:9px"><i></i>TERRAVANTA</div></div><div class="stripe"></div>
    <p class="abs" style="left:18px;top:54px;font-size:5.3px;font-weight:700">Lorem ipsum dolor sit amet, consectetur adipiscing elit.</p>
    <p class="abs txt" style="left:18px;top:76px;width:350px;line-height:1.9">Fusce sit amet neque sodales, faucibus ex eu, efficitur lacus. Cras imperdiet, nulla nec sagittis pulvinar, neque augue iaculis risus, ac fringilla felis urna fermentum mi. Ut vehicula vel enim sit amet vulputate. Aenean malesuada consectetur diam, ac convallis quam tincidunt eget. Nam vitae elementum ipsum. Proin vitae blandit enim. Donec congue convallis commodo. Aenean vel lacus lacus. Sed in erat ultrices dolor faucibus feugiat. Nullam cursus sollicitudin dolor. Donec a ex et enim consectetur auctor. Aliquam ut laoreet neque. Aenean molestie, libero sed suscipit tincidunt, tellus nulla dolor dui, in viverra nunc purus sodales diam. Sed ullamcorper et ante eget euismod. Sed in erat ultrices dolor faucibus feugiat. Nullam cursus sollicitudin dolor. Donec a ex et enim consectetur auctor. Aliquam ut laoreet neque.</p>
    <p class="abs txt" style="left:18px;top:150px;width:350px;line-height:1.9">Maecenas in purus et tellus tincidunt sodales eu sed nibh. Aenean justo diam, commodo vel felis ac, malesuada sodales purus. Nunc sollicitudin sed justo in eleifend. Fusce dictum, ornare ligula, eu porttitor elit ullamcorper non. Aliquam erat volutpat. Mauris malesuada turpis non tellus scelerisque tempus. Morbi dui turpis, mollis a ultrices blandit, commodo a enim. Mauris sit amet eleifend sapien.</p>
    <div class="foot-stripe"></div><div class="foot"></div><p class="copy">Copyright © 2020 Terravanta | All rights reserved</p>
  </article>

  <article class="slide" style="left:408px;top:727px">
    <div class="photo" style="left:0;top:0;width:145px;height:208px;background:linear-gradient(180deg,#8c8c86,#b9a454 55%,#d9b23a)" role="img" aria-label="Bearded activist in a yellow raincoat holding a 'Save our Planet' sign"></div>
    <div class="brand" style="right:10px;top:10px"><i></i>TERRAVANTA</div>
    <div class="navy-box" style="left:120px;top:28px;width:180px;height:22px;font-size:6.8px;font-weight:700;color:var(--sun);line-height:22px;padding-left:18px">LOREM IPSUM CONSECTETUR</div>
    <p class="abs txt" style="left:180px;top:84px;width:186px;color:var(--ink)">Business valuation is a process and a set of procedures used to estimate the economic value of an owner's interest in a business. Valuation is used by financial market participants to determine the price they are willing to pay or receive to effect a sale of a business.</p>
    <svg class="abs" style="left:180px;top:130px" width="8" height="8" viewBox="0 0 8 8"><path d="M1 7h6M2 6l4-4 1 1-4 4H2z" stroke="var(--amber)" stroke-width=".8" fill="none"/></svg>
    <svg class="abs" style="left:278px;top:130px" width="8" height="8" viewBox="0 0 8 8"><path d="M1 4l6-3-2 6-1-2z" fill="var(--navy)"/></svg>
    <p class="abs" style="left:180px;top:143px;font-size:5px;color:var(--amber);font-weight:600">Your Contents Here</p>
    <p class="abs txt" style="left:180px;top:152px;width:85px;color:var(--ink)">Lorem ipsum dolor sit amet, consectetur adipiscing elit, sed do eiusmod tempor incididunt.</p>
    <p class="abs" style="left:278px;top:143px;font-size:5px;color:var(--amber);font-weight:600">Your Contents Here</p>
    <p class="abs txt" style="left:278px;top:152px;width:88px;color:var(--ink)">Lorem ipsum dolor sit amet, consectetur adipiscing elit, sed do eiusmod tempor incididunt.</p>
    <div class="foot-stripe"></div><div class="foot"></div><p class="copy" style="color:var(--paper);bottom:0">Copyright © 2020 Terravanta | All rights reserved</p>
  </article>

  <article class="slide" style="left:804px;top:727px">
    <div class="head"><h3>TWO BULLET POINTS</h3><p class="tag">HERE ADD YOUR TITLE</p><div class="brand"><i></i>TERRAVANTA</div></div><div class="stripe"></div>
    <div class="navy-box" style="left:40px;top:86px;width:138px;height:64px;border-radius:7px;display:flex;align-items:center;justify-content:center;text-align:center;font-size:5.6px;font-weight:700;padding:0 14px;line-height:1.5;box-shadow:0 3px 6px rgba(0,0,0,.25)">Lorem Ipsum is simply dummy unknown printer took a galley of type and scrambled it to make.</div>
    <div class="navy-box" style="left:213px;top:86px;width:138px;height:64px;border-radius:7px;display:flex;align-items:center;justify-content:center;text-align:center;font-size:5.6px;font-weight:700;padding:0 14px;line-height:1.5;box-shadow:0 3px 6px rgba(0,0,0,.25)">Lorem Ipsum is simply dummy unknown printer took a galley of type and scrambled it to make.</div>
    <div class="foot-stripe"></div><div class="foot"></div><p class="copy">Copyright © 2020 Terravanta | All rights reserved</p>
  </article>

  <!-- Row 3 -->
  <article class="slide" style="left:13px;top:962px">
    <div class="head"><h3>FOUR BULLET POINTS AND PICTURE</h3><p class="tag">HERE ADD YOUR TITLE</p><div class="brand"><i></i>TERRAVANTA</div></div><div class="stripe"></div>
    <div class="dot" style="left:30px;top:58px;width:18px;height:18px;background:var(--green)"></div>
    <div class="dot" style="left:30px;top:93px;width:18px;height:18px;background:var(--green)"></div>
    <div class="dot" style="left:30px;top:128px;width:18px;height:18px;background:var(--green)"></div>
    <div class="dot" style="left:30px;top:163px;width:18px;height:18px;background:var(--green)"></div>
    <div class="abs" style="left:62px;top:56px;width:95px"><p class="lbl">Your Text Here</p><p class="txt">Lorem ipsum dolor sit amet, nec an dictas equidem appetere, ut has commune accommodare. Mea illum, iusto solet opta.</p></div>
    <div class="abs" style="left:62px;top:91px;width:95px"><p class="lbl">Your Text Here</p><p class="txt">Lorem ipsum dolor sit amet, nec an dictas equidem appetere, ut has commune accommodare. Mea illum, iusto solet opta.</p></div>
    <div class="abs" style="left:62px;top:126px;width:95px"><p class="lbl">Your Text Here</p><p class="txt">Lorem ipsum dolor sit amet, nec an dictas equidem appetere, ut has commune accommodare. Mea illum, iusto solet opta.</p></div>
    <div class="abs" style="left:62px;top:161px;width:95px"><p class="lbl">Your Text Here</p><p class="txt">Lorem ipsum dolor sit amet, nec an dictas equidem appetere, ut has commune accommodare. Mea illum, iusto solet opta.</p></div>
    <div class="photo" style="left:212px;top:50px;width:135px;height:135px;border-radius:50%;background:radial-gradient(circle at 45% 55%,#2b9fd3,#36a43a 70%,#9fd04a)" role="img" aria-label="Illustrated globe with green leaves growing from the top"></div>
    <div class="foot-stripe"></div><div class="foot"></div><p class="copy">Copyright © 2020 Terravanta | All rights reserved</p>
  </article>

  <article class="slide" style="left:408px;top:962px">
    <div class="head"><h3>ADD YOUR AWESOME TITLE HERE</h3><p class="tag">HERE ADD YOUR TITLE</p><div class="brand"><i></i>TERRAVANTA</div></div><div class="stripe"></div>
    <div class="dot" style="left:17px;top:64px;width:15px;height:15px;background:var(--green);font-size:5px">1</div>
    <div class="dot" style="left:17px;top:101px;width:15px;height:15px;background:var(--green);font-size:5px">2</div>
    <div class="dot" style="left:17px;top:138px;width:15px;height:15px;background:var(--green);font-size:5px">3</div>
    <div class="dot" style="left:17px;top:175px;width:15px;height:15px;background:var(--green);font-size:5px">4</div>
    <div class="abs" style="left:42px;top:56px;width:85px"><p class="lbl">Contents Title</p><p class="txt">Lorem ipsum randomised words which in some form, by injected humour or words which don't look even slightly.</p></div>
    <div class="abs" style="left:42px;top:93px;width:85px"><p class="lbl">Contents Title</p><p class="txt">Lorem ipsum randomised words which in some form, by injected humour or words which don't look even slightly.</p></div>
    <div class="abs" style="left:42px;top:130px;width:85px"><p class="lbl">Contents Title</p><p class="txt">Lorem ipsum randomised words which in some form, by injected humour or words which don't look even slightly.</p></div>
    <div class="abs" style="left:42px;top:167px;width:85px"><p class="lbl">Contents Title</p><p class="txt">Lorem ipsum randomised words which don't look even slightly believe in some form, by injected humour.</p></div>
    <div class="photo" style="left:148px;top:80px;width:88px;height:126px;border-radius:40px 40px 0 0;background:linear-gradient(180deg,#8cc640,#3b9f38 70%,#7b6a55)" role="img" aria-label="Illustration of a slender green tree"></div>
    <div class="dot" style="left:250px;top:64px;width:15px;height:15px;background:#8a8f96;font-size:5px">1</div>
    <div class="dot" style="left:250px;top:101px;width:15px;height:15px;background:#8a8f96;font-size:5px">2</div>
    <div class="dot" style="left:250px;top:138px;width:15px;height:15px;background:#8a8f96;font-size:5px">3</div>
    <div class="dot" style="left:250px;top:175px;width:15px;height:15px;background:#8a8f96;font-size:5px">4</div>
    <div class="abs" style="left:277px;top:56px;width:88px"><p class="lbl">Contents Title</p><p class="txt">Lorem ipsum randomised words which don't in some form, by injected humour or words which don't look.</p></div>
    <div class="abs" style="left:277px;top:93px;width:88px"><p class="lbl">Contents Title</p><p class="txt">Lorem ipsum randomised words which in some form, by injected humour or words which don't look slightly.</p></div>
    <div class="abs" style="left:277px;top:130px;width:88px"><p class="lbl">Contents Title</p><p class="txt">Lorem ipsum randomised words alteration in some form, by injected humour or words which don't look.</p></div>
    <div class="abs" style="left:277px;top:167px;width:88px"><p class="lbl">Contents Title</p><p class="txt">Lorem ipsum randomised words which don't in some form, by injected humour or words which don't look.</p></div>
    <div class="foot-stripe"></div><div class="foot"></div><p class="copy">Copyright © 2020 Terravanta | All rights reserved</p>
  </article>

  <article class="slide" style="left:804px;top:962px">
    <div class="head"><h3>SIX POINTS</h3><p class="tag">HERE ADD YOUR TITLE</p><div class="brand"><i></i>TERRAVANTA</div></div><div class="stripe"></div>
    <div class="dot" style="left:20px;top:87px;width:15px;height:15px;background:var(--green);font-size:4.5px">01</div>
    <div class="dot" style="left:140px;top:89px;width:15px;height:15px;background:var(--green);font-size:4.5px">02</div>
    <div class="dot" style="left:264px;top:89px;width:15px;height:15px;background:var(--green);font-size:4.5px">03</div>
    <div class="dot" style="left:20px;top:140px;width:15px;height:15px;background:var(--green);font-size:4.5px">04</div>
    <div class="dot" style="left:140px;top:140px;width:15px;height:15px;background:var(--green);font-size:4.5px">05</div>
    <div class="dot" style="left:264px;top:140px;width:15px;height:15px;background:var(--green);font-size:4.5px">06</div>
    <div class="abs" style="left:45px;top:78px;width:85px"><p class="lbl">Project name</p><p class="txt">Lorem ipsum is simply dummy unknown printer took a galley of type and scrambled it to make.</p></div>
    <div class="abs" style="left:165px;top:80px;width:85px"><p class="lbl">Project name</p><p class="txt">Lorem ipsum is simply dummy unknown printer took a galley of type and scrambled it to make.</p></div>
    <div class="abs" style="left:289px;top:80px;width:85px"><p class="lbl">Project name</p><p class="txt">Lorem ipsum is simply dummy unknown printer took a galley of type and scrambled it to make.</p></div>
    <div class="abs" style="left:45px;top:131px;width:85px"><p class="lbl">Project name</p><p class="txt">Lorem ipsum is simply dummy unknown printer took a galley of type and scrambled it to make.</p></div>
    <div class="abs" style="left:165px;top:131px;width:85px"><p class="lbl">Project name</p><p class="txt">Lorem ipsum is simply dummy unknown printer took a galley of type and scrambled it to make.</p></div>
    <div class="abs" style="left:289px;top:131px;width:85px"><p class="lbl">Project name</p><p class="txt">Lorem ipsum is simply dummy unknown printer took a galley of type and scrambled it to make.</p></div>
    <div class="foot-stripe"></div><div class="foot"></div><p class="copy">Copyright © 2020 Terravanta | All rights reserved</p>
  </article>

  <!-- Row 4 -->
  <article class="slide" style="left:13px;top:1192px">
    <div class="abs" style="left:42px;top:32px;width:40px;height:2px;background:var(--navy)"></div>
    <p class="abs" style="left:42px;top:38px;width:150px;font-size:8.3px;font-weight:500;color:var(--navy);line-height:1.3">Success is not only what you achieve in your life, but also what you inspire in the lives of others</p>
    <div class="photo" style="left:0;top:107px;width:384px;height:108px;background:linear-gradient(90deg,#1d3257,#2a4369 55%,#1d3257)" role="img" aria-label="Faint photo of a business team in a meeting over a navy overlay"></div>
    <div class="abs" style="left:35px;top:138px;width:100px;color:var(--paper)"><p style="font-size:5.4px;font-weight:700">Lorem ipsum dolor</p><p style="font-size:4.3px;margin-top:8px;opacity:.85">Lorem ipsum dolor sit amet, consectetur adipiscing elit, sed do eiusmod tempor</p></div>
    <div class="abs" style="left:148px;top:138px;width:100px;color:var(--paper)"><p style="font-size:5.4px;font-weight:700">Lorem ipsum dolor</p><p style="font-size:4.3px;margin-top:8px;opacity:.85">Lorem ipsum dolor sit amet, consectetur adipiscing elit, sed do eiusmod tempor</p></div>
    <div class="abs" style="left:258px;top:138px;width:105px;color:var(--paper)"><p style="font-size:5.4px;font-weight:700">Lorem ipsum dolor</p><p style="font-size:4.3px;margin-top:8px;opacity:.85">Lorem ipsum dolor sit amet, consectetur adipiscing elit, sed do eiusmod tempor</p></div>
  </article>

  <article class="slide" style="left:408px;top:1192px">
    <div class="head"><h3>ADD YOUR AWESOME TITLE HERE</h3><p class="tag">HERE ADD YOUR TITLE</p><div class="brand"><i></i>TERRAVANTA</div></div><div class="stripe"></div>
    <div class="card" style="left:48px;background:linear-gradient(180deg,var(--sun),var(--amber))"><div class="disc"></div><b>Your Contents Here</b><p>Lorem ipsum dolor sit amet, consectetur adipiscing elit, sed do eiusmod tempor incididunt.</p></div>
    <div class="card" style="left:148px;background:linear-gradient(180deg,var(--lime),var(--green))"><div class="disc"></div><b>Your Contents Here</b><p>Lorem ipsum dolor sit amet, consectetur adipiscing elit, sed do eiusmod tempor incididunt.</p></div>
    <div class="card" style="left:248px;background:linear-gradient(180deg,var(--sky),var(--blue))"><div class="disc"></div><b>Your Contents Here</b><p>Lorem ipsum dolor sit amet, consectetur adipiscing elit, sed do eiusmod tempor incididunt.</p></div>
    <div class="foot-stripe"></div><div class="foot"></div><p class="copy">Copyright © 2020 Terravanta | All rights reserved</p>
  </article>

  <article class="slide" style="left:804px;top:1192px">
    <div class="head"><h3>TIMELINE</h3><p class="tag">HERE ADD YOUR TITLE</p><div class="brand"><i></i>TERRAVANTA</div></div><div class="stripe"></div>
    <div class="abs" style="left:38px;top:97px;width:310px;height:1px;background:#c9ced6"></div>
    <svg class="abs" style="left:0;top:0" width="384" height="215">
      <circle cx="38" cy="97" r="4.5" fill="var(--lime)"/><circle cx="100" cy="97" r="4.5" fill="var(--blue)"/><circle cx="162" cy="97" r="4.5" fill="var(--sun)"/>
      <circle cx="224" cy="97" r="4.5" fill="var(--lime)"/><circle cx="286" cy="97" r="4.5" fill="var(--blue)"/><circle cx="348" cy="97" r="4.5" fill="var(--sun)"/>
    </svg>
    <p class="abs lbl" style="left:29px;top:82px">2015</p><p class="abs lbl" style="left:91px;top:82px">2016</p><p class="abs lbl" style="left:153px;top:83px">2017</p>
    <p class="abs lbl" style="left:215px;top:80px">2018</p><p class="abs lbl" style="left:277px;top:81px">2019</p><p class="abs lbl" style="left:339px;top:81px">2020</p>
    <div class="abs" style="left:14px;top:129px;width:50px;text-align:center"><p class="lbl" style="font-size:4.2px">Project name</p><p class="txt">Lorem ipsum is simply dummy unknown printer took a galley of type and scrambled it to make.</p></div>
    <div class="abs" style="left:76px;top:129px;width:50px;text-align:center"><p class="lbl" style="font-size:4.2px">Project name</p><p class="txt">Lorem ipsum is simply dummy unknown printer took a galley of type and scrambled it to make.</p></div>
    <div class="abs" style="left:138px;top:129px;width:50px;text-align:center"><p class="lbl" style="font-size:4.2px">Project name</p><p class="txt">Lorem ipsum is simply dummy unknown printer took a galley of type and scrambled it to make.</p></div>
    <div class="abs" style="left:200px;top:129px;width:50px;text-align:center"><p class="lbl" style="font-size:4.2px">Project name</p><p class="txt">Lorem ipsum is simply dummy unknown printer took a galley of type and scrambled it to make.</p></div>
    <div class="abs" style="left:262px;top:129px;width:50px;text-align:center"><p class="lbl" style="font-size:4.2px">Project name</p><p class="txt">Lorem ipsum is simply dummy unknown printer took a galley of type and scrambled it to make.</p></div>
    <div class="abs" style="left:324px;top:129px;width:50px;text-align:center"><p class="lbl" style="font-size:4.2px">Project name</p><p class="txt">Lorem ipsum is simply dummy unknown printer took a galley of type and scrambled it to make.</p></div>
    <div class="foot-stripe"></div><div class="foot"></div><p class="copy">Copyright © 2020 Terravanta | All rights reserved</p>
  </article>

  <!-- Row 5 -->
  <article class="slide" style="left:13px;top:1422px">
    <div class="head"><h3>INFOGRAPHIC</h3><p class="tag">HERE ADD YOUR TITLE</p><div class="brand"><i></i>TERRAVANTA</div></div><div class="stripe"></div>
    <svg class="abs" style="left:0;top:0" width="384" height="215">
      <circle cx="192" cy="120" r="56" fill="none" stroke="#b8c0cc" stroke-width=".7" stroke-dasharray="2 2"/>
      <circle cx="192" cy="120" r="43" fill="var(--navy)"/>
      <g fill="var(--paper)" stroke-width="1.2">
        <circle cx="145" cy="90" r="3.5" stroke="var(--lime)"/><circle cx="139" cy="120" r="3.5" stroke="var(--lime)"/><circle cx="145" cy="150" r="3.5" stroke="var(--blue)"/>
        <circle cx="239" cy="90" r="3.5" stroke="var(--blue)"/><circle cx="245" cy="120" r="3.5" stroke="var(--lime)"/><circle cx="239" cy="150" r="3.5" stroke="var(--amber)"/>
      </g>
    </svg>
    <p class="abs" style="left:152px;top:108px;width:80px;text-align:center;font-size:6.5px;font-weight:700;color:var(--paper);line-height:1.3">Add Your Awesome Title Here</p>
    <div class="tile" style="left:63px;top:79px;background:linear-gradient(90deg,var(--sun),var(--amber))">Composition of the Board</div>
    <div class="tile" style="left:55px;top:110px;background:linear-gradient(90deg,var(--lime),var(--green))">Clarity of roles &amp; responsibilities</div>
    <div class="tile" style="left:63px;top:141px;background:linear-gradient(90deg,var(--sky),var(--blue))">Joint vision</div>
    <div class="tile" style="left:259px;top:79px;background:linear-gradient(90deg,var(--sky),var(--blue))">Ability to use the strengths of all members</div>
    <div class="tile" style="left:263px;top:110px;background:linear-gradient(90deg,var(--lime),var(--green))">Ability to resolve conflicts between the Board &amp; staff</div>
    <div class="tile" style="left:259px;top:141px;background:linear-gradient(90deg,var(--sun),var(--amber))">Structure &amp; organisation of the work</div>
    <div class="foot-stripe"></div><div class="foot"></div><p class="copy">Copyright © 2020 Terravanta | All rights reserved</p>
  </article>

  <article class="slide" style="left:408px;top:1422px">
    <div class="photo" style="left:124px;top:14px;width:246px;height:186px;border-radius:10px;background:linear-gradient(135deg,#3d5780,#1d3257)" role="img" aria-label="Navy world map with highlighted locations in North America, Europe and Australia"></div>
    <div class="brand" style="right:10px;top:10px;color:var(--paper)"><i></i>TERRAVANTA</div>
    <p class="abs" style="left:24px;top:148px;width:95px;font-size:11px;font-weight:500;color:var(--navy);line-height:1.3">Add Your Awesome Title Here</p>
    <div class="foot-stripe"></div><div class="foot"></div><p class="copy">Copyright © 2020 Terravanta | All rights reserved</p>
  </article>

  <article class="slide" style="left:804px;top:1422px">
    <p class="abs" style="left:0;width:384px;top:12px;text-align:center;font-size:12px;font-weight:500;color:var(--navy)">OUR TEAM</p>
    <p class="abs" style="left:0;width:384px;top:27px;text-align:center;font-size:4.5px;font-weight:700;color:var(--blue);letter-spacing:1.5px">HERE ADD YOUR TITLE</p>
    <div class="brand" style="right:8px;top:12px"><i></i>TERRAVANTA</div>
    <div class="team" style="left:12px"><div class="face"></div><b>Your Name</b><em>Founder</em><p class="txt">Lorem ipsum dolor sit amet, consectetur adipiscing elit. Donec mauris lorem, vestibulum ac rutrum id, suscipit in dui.</p><span class="line" style="background:var(--lime)"></span></div>
    <div class="team" style="left:102px;background:var(--mist)"><div class="face"></div><b>Your Name</b><em>Global Account Executive</em><p class="txt">Lorem ipsum dolor sit amet, consectetur adipiscing elit. Donec mauris lorem, vestibulum ac rutrum id, suscipit in dui.</p><span class="line" style="background:var(--blue)"></span></div>
    <div class="team" style="left:196px"><div class="face"></div><b>Your Name</b><em>Founder</em><p class="txt">Lorem ipsum dolor sit amet, consectetur adipiscing elit. Donec mauris lorem, vestibulum ac rutrum id, suscipit in dui.</p><span class="line" style="background:var(--navy)"></span></div>
    <div class="team" style="left:286px;background:var(--mist)"><div class="face"></div><b>Your Name</b><em>Global Account Executive</em><p class="txt">Lorem ipsum dolor sit amet, consectetur adipiscing elit. Donec mauris lorem, vestibulum ac rutrum id, suscipit in dui.</p><span class="line" style="background:var(--lime)"></span></div>
    <div class="foot-stripe"></div><div class="foot"></div><p class="copy">Copyright © 2020 Terravanta | All rights reserved</p>
  </article>

  <!-- Row 6 -->
  <article class="slide" style="left:13px;top:1651px">
    <div class="head"><h3>YOUR AWESOME TEXT HERE</h3><p class="tag">HERE ADD YOUR TITLE</p><div class="brand"><i></i>TERRAVANTA</div></div><div class="stripe"></div>
    <div class="tile" style="left:28px;top:58px;height:23px;font-weight:700;font-size:4.5px;background:linear-gradient(90deg,var(--sun),var(--amber))">Business valuation</div>
    <div class="tile" style="left:28px;top:87px;height:23px;font-weight:700;font-size:4.5px;background:linear-gradient(90deg,var(--lime),var(--green))">Business valuation</div>
    <div class="tile" style="left:28px;top:116px;height:23px;font-weight:700;font-size:4.5px;background:linear-gradient(90deg,var(--sun),var(--amber))">Business valuation</div>
    <div class="tile" style="left:28px;top:145px;height:23px;font-weight:700;font-size:4.5px;background:linear-gradient(90deg,var(--lime),var(--green))">Business valuation</div>
    <p class="abs txt" style="left:100px;top:60px;width:268px;color:var(--ink)">Lorem ipsum dolor sit amet, consectetur adipiscing elit, sed do eiusmod tempor incididunt ut labore et dolore magna aliqua. Lorem ipsum dolor sit amet, consectetur adipiscing elit, sed do eiusmod tempor incididunt ut labore et dolore magna aliqua. Ut enim ad minim veniam, quis nostrud exercitation ullamco laboris nisi ut aliquip.</p>
    <p class="abs txt" style="left:100px;top:89px;width:268px;color:var(--ink)">Lorem ipsum dolor sit amet, consectetur adipiscing elit, sed do eiusmod tempor incididunt ut labore et dolore magna aliqua. Lorem ipsum dolor sit amet, consectetur adipiscing elit, sed do eiusmod tempor incididunt ut labore et dolore magna aliqua. Ut enim ad minim veniam, quis nostrud exercitation ullamco laboris nisi ut aliquip.</p>
    <p class="abs txt" style="left:100px;top:118px;width:268px;color:var(--ink)">Lorem ipsum dolor sit amet, consectetur adipiscing elit, sed do eiusmod tempor incididunt ut labore et dolore magna aliqua. Lorem ipsum dolor sit amet, consectetur adipiscing elit, sed do eiusmod tempor incididunt ut labore et dolore magna aliqua. Ut enim ad minim veniam, quis nostrud exercitation ullamco laboris nisi ut aliquip.</p>
    <p class="abs txt" style="left:100px;top:147px;width:268px;color:var(--ink)">Lorem ipsum dolor sit amet, consectetur adipiscing elit, sed do eiusmod tempor incididunt ut labore et dolore magna aliqua. Lorem ipsum dolor sit amet, consectetur adipiscing elit, sed do eiusmod tempor incididunt ut labore et dolore magna aliqua. Ut enim ad minim veniam, quis nostrud exercitation ullamco laboris nisi ut aliquip.</p>
    <div class="foot-stripe"></div><div class="foot"></div><p class="copy">Copyright © 2020 Terravanta | All rights reserved</p>
  </article>

  <article class="slide" style="left:408px;top:1651px">
    <div class="head"><h3>ADD YOUR AWESOME TITLE HERE</h3><p class="tag">HERE ADD YOUR TITLE</p><div class="brand"><i></i>TERRAVANTA</div></div><div class="stripe"></div>
    <div class="abs" style="left:28px;top:45px;width:105px"><p class="lbl" style="font-weight:600">Lorem ipsum</p><p class="txt" style="color:var(--ink);margin-top:3px">• Lorem ipsum dolor sit amet, consecter adipiscing elit.<br>• Lorem ipsum dolor sit amet, consecter adipiscing elit. Maecas porttitor congue massa.</p></div>
    <div class="abs" style="left:143px;top:45px;width:105px"><p class="lbl" style="font-weight:600">Lorem ipsum</p><p class="txt" style="color:var(--ink);margin-top:3px">• Lorem ipsum dolor sit amet, consecter adipiscing elit.<br>• Lorem ipsum dolor sit amet, consecter adipiscing elit. Maecas porttitor congue massa.</p></div>
    <div class="abs" style="left:259px;top:45px;width:105px"><p class="lbl" style="font-weight:600">Lorem ipsum</p><p class="txt" style="color:var(--ink);margin-top:3px">• Lorem ipsum dolor sit amet, consecter adipiscing elit.<br>• Lorem ipsum dolor sit amet, consecter adipiscing elit. Maecas porttitor congue massa.</p></div>
    <table class="grid" style="left:15px;top:106px;width:354px">
      <tr><th>Text</th><th>Text</th><th>Text</th><th>Text</th><th style="background:var(--navy);color:var(--paper);font-size:3.6px">TERRAVANTA</th><th>Text</th></tr>
      <tr><td>Data</td><td>Data</td><td>Data</td><td>Data</td><td>Data</td><td>Data</td></tr>
      <tr><td>Data</td><td>Data</td><td>Data</td><td>Data</td><td>Data</td><td>Data</td></tr>
      <tr><td>Data</td><td>Data</td><td>Data</td><td>Data</td><td>Data</td><td>Data</td></tr>
      <tr><td>Data</td><td>Data</td><td>Data</td><td>Data</td><td>Data</td><td>Data</td></tr>
      <tr><td>Data</td><td>Data</td><td>Data</td><td>Data</td><td>Data</td><td>Data</td></tr>
    </table>
    <div class="foot-stripe"></div><div class="foot"></div><p class="copy">Copyright © 2020 Terravanta | All rights reserved</p>
  </article>

  <article class="slide" style="left:804px;top:1651px">
    <div class="head"><h3>STATISTIC</h3><p class="tag">HERE ADD YOUR TITLE</p><div class="brand"><i></i>TERRAVANTA</div></div><div class="stripe"></div>
    <p class="abs" style="left:0;width:384px;top:44px;text-align:center;font-size:15px;font-weight:500;color:var(--navy)">Your awesome text here</p>
    <p class="abs" style="left:77px;top:66px;width:230px;text-align:center;font-size:4.3px;color:var(--ink)">Lorem Ipsum is the printing and typesetting industry. Lorem Ipsum has been the industry's standard dummy text ever since the 1500s, when an unknown printer took a galley of type and scrambled it to make a type specimen book. It has survived not only five centuries.</p>
    <svg class="abs" style="left:0;top:0" width="384" height="215">
      <g fill="none" stroke-width="3.5" transform="rotate(-90)">
        <circle cx="-130" cy="108" r="19" stroke="#e3e6ea"/><circle cx="-130" cy="108" r="19" stroke="var(--lime)" stroke-dasharray="59.7 119.4"/>
        <circle cx="-130" cy="192" r="19" stroke="#e3e6ea"/><circle cx="-130" cy="192" r="19" stroke="var(--blue)" stroke-dasharray="89.5 119.4"/>
        <circle cx="-130" cy="274" r="19" stroke="#e3e6ea"/><circle cx="-130" cy="274" r="19" stroke="var(--sun)" stroke-dasharray="47.8 119.4"/>
      </g>
      <g font-family="Montserrat,sans-serif" font-size="10" font-weight="600" fill="var(--navy)" text-anchor="middle">
        <text x="108" y="134">50%</text><text x="192" y="134">75%</text><text x="274" y="134">40%</text>
      </g>
    </svg>
    <p class="abs" style="left:78px;top:166px;width:60px;text-align:center;font-size:3.8px;color:var(--ink)">Lorem ipsum dolor amet amet consectetur dolor</p>
    <p class="abs" style="left:162px;top:166px;width:60px;text-align:center;font-size:3.8px;color:var(--ink)">Lorem ipsum dolor amet amet consectetur dolor</p>
    <p class="abs" style="left:244px;top:166px;width:60px;text-align:center;font-size:3.8px;color:var(--ink)">Lorem ipsum dolor amet amet consectetur dolor</p>
    <div class="foot-stripe"></div><div class="foot"></div><p class="copy">Copyright © 2020 Terravanta | All rights reserved</p>
  </article>

  <!-- Row 7 -->
  <article class="slide" style="left:13px;top:1880px">
    <div class="brand" style="right:10px;top:12px"><i></i>TERRAVANTA</div>
    <p class="abs" style="left:26px;top:58px;font-size:11px;font-weight:500;color:var(--navy)">STEPS TO SUCCESS</p>
    <p class="abs" style="left:52px;top:73px;font-size:4.5px;color:var(--grey)">Write here a great subtitle</p>
    <div class="abs" style="left:52px;top:80px;width:30px;height:1px;background:var(--lime)"></div>
    <div class="photo" style="left:198px;top:8px;width:50px;height:65px;border-radius:22px 22px 6px 6px;background:linear-gradient(180deg,var(--lime),var(--green))" role="img" aria-label="Green pictogram figure climbing a step"></div>
    <div class="step" style="left:24px;top:140px;width:70px">01</div>
    <div class="step" style="left:92px;top:120px;width:72px">02</div>
    <div class="step" style="left:163px;top:99px;width:70px">03</div>
    <div class="step" style="left:233px;top:78px;width:70px">04</div>
    <div class="step" style="left:302px;top:56px;width:64px">05</div>
    <div class="abs" style="left:25px;top:152px;width:65px"><p class="lbl" style="font-weight:500">Lorem ipsum dolor</p><p class="txt">Lorem ipsum dolor sit amet, consectetur adipiscing elit, sed do eiusmod tempor</p></div>
    <div class="abs" style="left:95px;top:132px;width:65px"><p class="lbl" style="font-weight:500">Lorem ipsum dolor</p><p class="txt">Lorem ipsum dolor sit amet, consectetur adipiscing elit, sed do eiusmod tempor</p></div>
    <div class="abs" style="left:165px;top:111px;width:65px"><p class="lbl" style="font-weight:500">Lorem ipsum dolor</p><p class="txt">Lorem ipsum dolor sit amet, consectetur adipiscing elit, sed do eiusmod tempor</p></div>
    <div class="abs" style="left:235px;top:90px;width:65px"><p class="lbl" style="font-weight:500">Lorem ipsum dolor</p><p class="txt">Lorem ipsum dolor sit amet, consectetur adipiscing elit, sed do eiusmod tempor</p></div>
    <div class="abs" style="left:304px;top:68px;width:65px"><p class="lbl" style="font-weight:500">Lorem ipsum dolor</p><p class="txt">Lorem ipsum dolor sit amet, consectetur adipiscing elit, sed do eiusmod tempor</p></div>
    <div class="foot-stripe"></div><div class="foot"></div><p class="copy">Copyright © 2020 Terravanta | All rights reserved</p>
  </article>

  <article class="slide" style="left:408px;top:1880px">
    <div class="head"><h3>STATISTIC AND TEXT</h3><p class="tag">HERE ADD YOUR TITLE</p><div class="brand"><i></i>TERRAVANTA</div></div><div class="stripe"></div>
    <svg class="abs" style="left:12px;top:42px" width="230" height="150" viewBox="0 0 230 150">
      <g stroke="#d5d9de" stroke-width=".5"><line x1="12" y1="4" x2="12" y2="110"/><line x1="12" y1="110" x2="225" y2="110"/></g>
      <g font-family="Montserrat,sans-serif" font-size="3.5" fill="var(--grey)">
        <text x="6" y="6">5</text><text x="6" y="27">4</text><text x="6" y="48">3</text><text x="6" y="69">2</text><text x="6" y="90">1</text><text x="6" y="111">0</text>
        <text x="28" y="118">Category 1</text><text x="81" y="118">Category 2</text><text x="135" y="118">Category 3</text><text x="188" y="118">Category 4</text>
        <text x="82" y="135">■ Series 1   ■ Series 2   ■ Series 3</text>
      </g>
      <rect x="24" y="40" width="9" height="70" fill="var(--green)"/><rect x="35" y="72" width="9" height="38" fill="var(--blue)"/><rect x="46" y="80" width="9" height="30" fill="var(--sun)"/>
      <rect x="78" y="75" width="9" height="35" fill="var(--green)"/><rect x="89" y="33" width="9" height="77" fill="var(--blue)"/><rect x="100" y="80" width="9" height="30" fill="var(--sun)"/>
      <rect x="131" y="56" width="9" height="54" fill="var(--green)"/><rect x="142" y="86" width="9" height="24" fill="var(--blue)"/><rect x="153" y="34" width="9" height="76" fill="var(--sun)"/>
      <rect x="185" y="44" width="9" height="66" fill="var(--green)"/><rect x="196" y="66" width="9" height="44" fill="var(--blue)"/><rect x="207" y="12" width="9" height="98" fill="var(--sun)"/>
    </svg>
    <div class="abs" style="left:250px;top:40px;width:122px;height:152px;background:var(--mist)"></div>
    <div class="dot" style="left:262px;top:53px;width:18px;height:18px;background:var(--green)"></div>
    <div class="dot" style="left:262px;top:93px;width:18px;height:18px;background:var(--green)"></div>
    <div class="dot" style="left:262px;top:133px;width:18px;height:18px;background:var(--green)"></div>
    <div class="abs" style="left:287px;top:51px;width:80px"><p style="font-size:5.5px;color:var(--ink)">Projectname</p><p class="txt">Lorem ipsum dolor sit amet, nec an dictas equidem appetere, ut has commune accommodare. Mea illum, iusto solet opta.</p></div>
    <div class="abs" style="left:287px;top:91px;width:80px"><p style="font-size:5.5px;color:var(--ink)">Projectname</p><p class="txt">Lorem ipsum dolor sit amet, nec an dictas equidem appetere, ut has commune accommodare. Mea illum, iusto solet opta.</p></div>
    <div class="abs" style="left:287px;top:131px;width:80px"><p style="font-size:5.5px;color:var(--ink)">Projectname</p><p class="txt">Lorem ipsum dolor sit amet, nec an dictas equidem appetere, ut has commune accommodare. Mea illum, iusto solet opta.</p></div>
    <div class="foot-stripe"></div><div class="foot"></div><p class="copy">Copyright © 2020 Terravanta | All rights reserved</p>
  </article>

  <article class="slide" style="left:804px;top:1880px">
    <div class="head"><h3>ADD YOUR AWESOME TITLE HERE</h3><p class="tag">HERE ADD YOUR TITLE</p><div class="brand"><i></i>TERRAVANTA</div></div><div class="stripe"></div>
    <table class="plan grid" style="left:35px;top:55px;width:316px;text-align:left">
      <tr><th>ADD YOUR TITLE</th><th>ADD YOUR TITLE</th><th style="background:var(--paper);color:var(--navy);border:1px solid var(--navy)">● TERRAVANTA</th><th>ADD YOUR TITLE</th></tr>
      <tr><td><b>Project name</b><p class="txt">Lorem ipsum is simply dummy unknown printer took a galley of type and scrambled it to make.</p></td><td><b>Project name</b><p class="txt">Lorem ipsum is simply dummy unknown printer took a galley of type and scrambled it to make.</p></td><td class="hl"><b>Project name</b><p class="txt">Lorem ipsum is simply dummy unknown printer took a galley of type and scrambled it to make.</p></td><td><b>Project name</b><p class="txt">Lorem ipsum is simply dummy unknown printer took a galley of type and scrambled it to make.</p></td></tr>
      <tr><td><b>Project name</b><p class="txt">Lorem ipsum is simply dummy unknown printer took a galley of type and scrambled it to make.</p></td><td><b>Project name</b><p class="txt">Lorem ipsum is simply dummy unknown printer took a galley of type and scrambled it to make.</p></td><td class="hl"><b>Project name</b><p class="txt">Lorem ipsum is simply dummy unknown printer took a galley of type and scrambled it to make.</p></td><td><b>Project name</b><p class="txt">Lorem ipsum is simply dummy unknown printer took a galley of type and scrambled it to make.</p></td></tr>
    </table>
    <div class="foot-stripe"></div><div class="foot"></div><p class="copy">Copyright © 2020 Terravanta | All rights reserved</p>
  </article>

  <!-- Closing -->
  <article class="slide" style="left:408px;top:2109px">
    <div class="photo" style="left:0;top:0;width:384px;height:200px;background:linear-gradient(180deg,#f7f8f9,#eef0f2)" role="img" aria-label="Faded photo of colleagues working together"></div>
    <div class="brand" style="left:152px;top:64px"><i></i>TERRAVANTA</div>
    <p class="abs" style="left:0;width:384px;top:111px;text-align:center;font-size:11.5px;font-weight:500;color:var(--navy)">CONNECTING EVIDENCE AND ACTION</p>
    <p class="abs" style="left:72px;top:131px;width:240px;text-align:center;font-size:4.3px;color:var(--ink)">Lorem ipsum dolor sit amet, consectetur adipiscing elit, sed do eiusmod tempor incididunt ut labore et dolore magna aliqua. Lorem ipsum dolor sit amet, consectetur adipiscing elit, sed do eiusmod tempor incididunt ut labore et dolore magna aliqua.</p>
    <div class="abs" style="left:0;bottom:15px;width:384px;height:2px;background:linear-gradient(90deg,var(--paper) 0 40%,var(--lime) 40% 62%,var(--sky) 62% 82%,var(--sun) 82%)"></div>
    <div class="navy-box" style="left:0;bottom:0;width:384px;height:15px"></div>
  </article>

</main>
</body>
</html>
```